Accounting firm needing business card / letterhead designed
Marcus L. Trenholm, CPA
marcus@veltrowledger.com
www.veltrowledger.com
842 E Alder Ave Maplecrest, VT 43827
802-562-0974

```html
<!DOCTYPE html>
<html lang="en">
<head>
<meta charset="utf-8">
<title>Veltro Ledger – Business Card</title>
<link rel="stylesheet" href="https://fonts.googleapis.com/css2?family=Roboto:wght@400;500;700&family=Roboto+Condensed:wght@500&display=swap">
<style>
  :root {
    --navy: #232060;
    --green: #82bd3c;
    --paper: #f4f4f4;
    --ink: #4a4a4a;
    --rule: #6a6a6a;
    --stage: #d9d6d1;
    --white: #ffffff;
  }
  * { margin: 0; padding: 0; box-sizing: border-box; }
  html, body { width: 1200px; height: 960px; overflow: hidden; }
  body {
    background: var(--stage);
    position: relative;
    font-family: "Roboto", Arial, sans-serif;
  }
  .card {
    position: absolute;
    width: 600px;
    height: 344px;
    box-shadow: 0 2px 6px rgba(0,0,0,0.35);
    overflow: hidden;
  }
  .card-front { left: 314px; top: 113px; background: var(--paper); }
  .card-back { left: 311px; top: 472px; background: var(--navy); }

  .brand-name {
    position: absolute;
    font-family: "Roboto", Arial, sans-serif;
    font-weight: 700;
    letter-spacing: 2px;
    white-space: nowrap;
  }
  .card-front .brand-name {
    left: 52px; top: 62px;
    font-size: 38px;
    color: var(--navy);
  }
  .card-back .brand-name {
    left: 0; right: 0; top: 112px;
    text-align: center;
    font-size: 48px;
    color: var(--white);
  }

  .name-accent {
    position: absolute;
    left: 0; top: 185px;
    width: 12px; height: 32px;
    background: var(--green);
  }
  .person-name {
    position: absolute;
    left: 48px; top: 188px;
    font-family: "Roboto Condensed", "Arial Narrow", sans-serif;
    font-weight: 500;
    font-size: 21px;
    color: var(--navy);
  }

  .contact-list {
    position: absolute;
    left: 48px; top: 241px;
    list-style: none;
    font-size: 14.5px;
    color: var(--ink);
    line-height: 19px;
  }
  .contact-list li { display: flex; align-items: center; gap: 8px; }
  .contact-list svg { width: 13px; height: 13px; fill: var(--navy); flex: none; }

  .address {
    position: absolute;
    left: 256px; top: 260px;
    padding-left: 18px;
    border-left: 1px solid var(--rule);
    font-size: 14.5px;
    line-height: 19px;
    color: var(--ink);
    font-style: normal;
  }

  .web-band {
    position: absolute;
    left: 0; top: 278px;
    width: 100%; height: 37px;
    background: var(--green);
    color: var(--white);
    text-align: center;
    font-size: 15px;
    line-height: 37px;
    letter-spacing: 6px;
  }
  .web-band strong { font-weight: 700; }
</style>
</head>
<body>

<section class="card card-front" aria-label="Business card front">
  <div class="brand-name">VELTRO LEDGER</div>
  <span class="name-accent"></span>
  <h1 class="person-name">Marcus L. Trenholm, CPA</h1>
  <ul class="contact-list">
    <li>
      <svg viewBox="0 0 16 16" aria-hidden="true"><path d="M3.6 1.2 6 3.6c.4.4.4 1 0 1.4L4.8 6.2a9 9 0 0 0 5 5L11 10c.4-.4 1-.4 1.4 0l2.4 2.4c.4.4.4 1 0 1.4l-1.3 1.3C11.8 16.8 0 5 1.3 3.5L2.2 1.2c.4-.4 1-.4 1.4 0z"/></svg>
      802-562-0974
    </li>
    <li>
      <svg viewBox="0 0 16 16" aria-hidden="true"><path d="M1 3h14v10H1z M2 4.2v.4l6 4 6-4v-.4z" fill-rule="evenodd"/></svg>
      marcus@veltrowledger.com
    </li>
    <li>
      <svg viewBox="0 0 16 16" aria-hidden="true"><circle cx="8" cy="8" r="7"/><path d="M5 4c2 1 1 3 3 3s1 3 3 4M4 11c1-1 2 0 3 1" stroke="#f4f4f4" stroke-width="1.3" fill="none"/></svg>
      www.veltrowledger.com
    </li>
  </ul>
  <address class="address">
    842 E Alder Ave<br>
    Maplecrest, VT 43827
  </address>
</section>

<section class="card card-back" aria-label="Business card back">
  <div class="brand-name">VELTRO LEDGER</div>
  <div class="web-band">www.<strong>veltrowledger</strong>.com</div>
</section>

</body>
</html>
```